Cool date project and tattoo

My children were born randomly on dates with a crazy number sequence and I am getting married on the next date in the sequence. The dates are as follows:

6/13/14
7/15/16
8/17/18
9/19/20.

I want a piece of art that has these dates beautifully drawn/written which I also would like to turn into a tattoo one day. I am not sure whether to add the kids names or not but would also be interested in seeing options. Here are the names of the kids and the wedding:

6/13/14 - Colby
7/15/16 - Fenna
8/17/18 - Mireth
9/19/20 - Wedding

I'd love to see options of how these dates could be presented in a unique and beautiful way!

I have not seen anything that I love yet..

Serif
Decorative
Script

• My project must have the dates included in the design
• I want to be able to see the dates relatively clearly, I want it to be able to not only be a large art project when printed on a large canvas, but also a cool looking tattoo.

Please check the color palates I added to see colors I like together.

```html
<!DOCTYPE html>
<html lang="en">
<head>
<meta charset="utf-8">
<title>Date Staircase</title>
<link rel="stylesheet" href="https://fonts.googleapis.com/css2?family=Allerta+Stencil&family=Montserrat:wght@500&display=swap">
<style>
  :root {
    --paper: #ffffff;
    --blush: #f28b8e;
    --slate: #2f5566;
    --label-text: #ffffff;
  }
  html, body {
    margin: 0;
    padding: 0;
    width: 1200px;
    height: 843px;
    overflow: hidden;
    background: var(--paper);
  }
  .artboard {
    display: block;
    width: 1200px;
    height: 843px;
  }
  .staircase { fill: var(--blush); }
  .date-digits {
    font-family: "Allerta Stencil", sans-serif;
    font-size: 58px;
    fill: var(--slate);
    text-anchor: middle;
    letter-spacing: 2px;
  }
  .month-digit {
    font-family: "Allerta Stencil", sans-serif;
    font-size: 60px;
    fill: var(--blush);
    text-anchor: middle;
  }
  .name-tag rect { fill: var(--slate); }
  .name-tag text {
    font-family: "Montserrat", sans-serif;
    font-weight: 500;
    font-size: 10px;
    letter-spacing: 1.6px;
    fill: var(--label-text);
    text-anchor: middle;
  }
</style>
</head>
<body>
<svg class="artboard" viewBox="0 0 700 492" xmlns="http://www.w3.org/2000/svg" aria-label="Dates 6/13/14, 7/15/16, 8/17/18 and 9/19/20 arranged as a staircase">
  <!-- stepped backdrop -->
  <polygon class="staircase"
    points="169,122 244,122 244,180 338,180 338,238 435,238 435,300 526,300 526,420 446,420 446,360 356,360 356,300 257,300 257,240 169,240"/>

  <!-- Colby: 6/13/14 -->
  <g class="name-tag">
    <rect x="180" y="58" width="65" height="15"/>
    <text x="212.5" y="69.5">COLBY</text>
  </g>
  <text class="month-digit" x="208" y="120">6</text>

  <!-- Fenna: 7/15/16 -->
  <g class="name-tag">
    <rect x="265" y="113" width="65" height="15"/>
    <text x="297.5" y="124.5">FENNA</text>
  </g>
  <text class="month-digit" x="294" y="175">7</text>

  <!-- Mireth: 8/17/18 -->
  <g class="name-tag">
    <rect x="359" y="173" width="64" height="15"/>
    <text x="391" y="184.5">MIRETH</text>
  </g>
  <text class="month-digit" x="391" y="235">8</text>

  <!-- Wedding: 9/19/20 -->
  <g class="name-tag">
    <rect x="451" y="234" width="70" height="15"/>
    <text x="486" y="245.5">WEDDING</text>
  </g>
  <text class="month-digit" x="484" y="296">9</text>

  <!-- day and year numbers -->
  <text class="date-digits" x="206" y="172">13</text>
  <text class="date-digits" x="206" y="232">14</text>
  <text class="date-digits" x="297" y="232">15</text>
  <text class="date-digits" x="297" y="292">16</text>
  <text class="date-digits" x="395" y="292">17</text>
  <text class="date-digits" x="395" y="352">18</text>
  <text class="date-digits" x="487" y="352">19</text>
  <text class="date-digits" x="487" y="412">20</text>
</svg>
</body>
</html>
```